New webdesign for a cable company

We need a new design for Lunor Media.

There exist a suggestion for the page, were we have attached files to show you this. The design here is not good enough, but here you can se what content we need.

You can feel free to give adjustment to this design to make it better, our blow us away with a new brilliant design, but from this design you see what content we need.

The important is that the company get a design who represent its products:
- TV = Cable TV
- Bredbånd = Broadband
- Mobil = Mobile phone
- Strøm = Electricity
- Alarm = Alarm
- Lunor Komplett = a cobain pagage of all our products.

Lunor Media would like costumers who visit the site to het the impression that Lunor Media is a professional, innovative and fun company.
Updates

We have to day uploaded pictures of the existing page as the link haven't been working for the most of you as it's placed on a server our developer are using and is often shut it down. 

We have also updated the brief with some new and updated description so please read true the updated brief. 

We will at the same time inform that we haven't been able to give feedback on any of the received design and are sorry for that, we will within the next 24 hours hopefully have started responded the different received designs.

Looking forward to see more suggestion and hope you will help us create and very professional and informative design. 

Reason: We have decided to extend the deadline due to the number of design suggestion who is sent in and your lack of response to all designers due to our own workload.

This project was unfortunately for different reason put on ice for a while, but we are now ready to complete the design and will answer and give feedback too all the received design suggestions. 

Within a couple of days we hope we have answered all you who sent us suggestions, we appreciate all suggestions and hope to get in more suggestions.

Reason: Deisgn description have been updated

Target Market(s)

Our costumer are both private and companies

Industry/Entity Type

Tv

Requirements
Must have
• A easy way to promote and inform about changes in our products, there are a constant change in our products and it must bee a easy and good way to changes ass the marked change. Cheek out this link, for a example of what we like/think of here, https://nett.fjordsignal.no

On all pages there must be a easy way to click on a order button and too inform about your interest (thats two different things), could be placed in the top right corner for example. In the order form you should follow a step by step part:
1. Cheek what product we can provide you.
2. Chooce products.
3. Costumer inforamtion.
4. Confirmation.

Somewere on the portal it must be possible for costumers to log on to their own administration, where they can cheek for invoices, other statuses, etc.

A main menu existing of:
Hjem (Home)
Produkter (Products)
Storkunde (key account/large costumers)
Kundeservice (Costumerservice)
Min side (My page)

The main menu should have the following sub titles:
- Under "Produkter"/products our different products must be listed
- Under "Kundeservice"/Costumerservice it must have these submenus:
- Hjelp og støtte = Help.
- Faktura = Invoice
- Brukerguider = Userguides
- Abbonementavtaler = Terms and conditions.

A bottom menu where we have 5 main categories, with sub categories:
Om oss (about us)
- Om Lunor Media (about Lunor Media)
- Kontaktinformajson ( contact information)
- Pressemeldinger (Pressrelese)
- Ledige stillinger (positions available)
- KRAV ( and organisastion in our field)

Produkter (Product)
- TV (TV)
- Bredbånd (Broadand)
- Telefoni (telephony, both mobil)
- Strøm (elecricity)
- Arlam (Alarm)

Borrettslag/Sameier (Housing cooperatives)
- Løsninger (solutions)
- Produkter (product)
- Kontaktpersoner (contactpersons)

Utbygger (developer)
- Hva vi kan gjøre for dere. (What we can do for you)

Opperatørnett (operators)

Build up the categories and bottom menu something like this:
https://nett.fjordsignal.no
www.brevix.com
Nice to have
• A main menu existing of:
Hjem (Home)
Produkter (Products)
Lunor Media
Kontakt oss (Contact us)

Under "Produkter"/products our different products must be listed and under "Kundeservice"/Costumerservice it must have these submenus:
- Hjelp og støtte = Help.
- Faktura = Invoice
Should not have
• Any translation section since the homepage only will be in Norwegian.

```html
<!DOCTYPE html>
<html lang="en">
<head>
<meta charset="utf-8">
<title>Lunor Media</title>
<link href="https://fonts.googleapis.com/css2?family=Ubuntu:ital,wght@0,400;0,500;0,700;1,400;1,500;1,700&family=Open+Sans:wght@400;600&display=swap" rel="stylesheet">
<style>
:root{
  --blue:#29aee6;
  --blue-dark:#0a96d4;
  --nav-top:#35bdf0;
  --nav-bottom:#0b9ad8;
  --green:#8cc81c;
  --green-dark:#76b40c;
  --promo-top:#4e93dc;
  --promo-bottom:#2c5fae;
  --text:#4a4a4a;
  --muted:#666;
  --black:#000;
  --white:#fff;
  --footer-top:#4f97e2;
  --footer-bottom:#2a6dc8;
}
*{box-sizing:border-box;margin:0;padding:0}
html,body{width:1200px;height:1134px;overflow:hidden}
body{position:relative;background:var(--white);font-family:"Open Sans",Arial,sans-serif;color:var(--text)}
.abs{position:absolute}
a{color:inherit;text-decoration:none}

.topbar{left:0;top:0;width:1200px;height:35px;background:var(--black)}
.topbar-links{right:109px;top:10px;font:400 11px "Ubuntu",sans-serif;color:var(--white)}
.topbar-links span{margin:0 4px}

.brand{left:110px;top:52px;display:flex;align-items:center;gap:14px}
.brand-dot{width:44px;height:44px;border-radius:50%;background:var(--blue)}
.brand-name{font:400 46px/1 "Ubuntu",sans-serif;color:var(--blue)}

.follow{left:943px;top:51px;font:500 14px "Ubuntu",sans-serif;color:#333}
.social{top:72px;width:26px;height:26px;border-radius:3px}
.social.s1{left:941px;background:#1c79b6}
.social.s2{left:977px;background:#3fb6e8}
.social.s3{left:1013px;background:#3c63a8}
.social.s4{left:1049px;background:#dcdcdc}

.mainnav{left:110px;top:128px;width:980px;height:44px;border-radius:3px;background:linear-gradient(var(--nav-top),var(--nav-bottom))}
.mainnav a{position:absolute;top:13px;font:500 15px "Ubuntu",sans-serif;color:var(--white)}
.nav-sep{position:absolute;top:0;width:1px;height:44px;background:rgba(0,70,120,.35);box-shadow:1px 0 0 rgba(255,255,255,.25)}
.search{left:740px;top:8px;width:229px;height:27px;border-radius:4px;background:var(--white);font:12px "Open Sans",sans-serif;color:#888;padding:6px 15px}
.search svg{position:absolute;right:8px;top:5px}

.hero{left:110px;top:185px;width:700px;height:343px;border-radius:3px;background:linear-gradient(90deg,#c9c9c9 0%,#e3e3e3 35%,#9c9c9c 70%,#bdbdbd 100%)}
.hero-line{position:absolute;left:5px;background:rgba(20,20,20,.88);color:var(--white);font:400 37px/42px "Ubuntu",sans-serif;padding:0 10px}
.hero-line b{font-weight:700}

.service{left:830px;width:260px;height:78px;border-radius:3px;background:linear-gradient(#62c0ea,#2e9ed5);color:var(--white)}
.service.green{background:linear-gradient(var(--green),var(--green-dark))}
.service.green .service-title{color:#111}
.service.green .service-text{color:#1d2a05}
.service-icon{position:absolute;left:14px;top:11px;width:56px;height:56px;border-radius:8px;background:linear-gradient(#fff,#dfe6ec);display:flex;align-items:center;justify-content:center}
.service-title{position:absolute;left:81px;top:12px;font:500 17px "Ubuntu",sans-serif;text-transform:uppercase}
.service-text{position:absolute;left:81px;top:33px;font:13px/14px "Ubuntu",sans-serif}
.service-arrow{position:absolute;right:16px;top:32px}

.welcome-title{left:119px;top:545px;font:italic 700 29px "Ubuntu",sans-serif;letter-spacing:-1px;color:var(--blue)}
.welcome-copy{left:120px;top:593px;width:690px;font:12.5px/18px "Open Sans",sans-serif;color:var(--text)}
.welcome-copy p+p{margin-top:19px}
.welcome-copy p:last-child{width:680px}

.featured-title{left:120px;top:740px;font:italic 400 25px "Ubuntu",sans-serif;letter-spacing:-1px;color:#555}
.featured-rule{left:212px;top:746px;width:597px;height:17px;background:repeating-linear-gradient(135deg,#e4e4e4 0 2px,transparent 2px 5px)}

.card{top:787px;width:220px;height:260px;background:var(--white);border:1px solid #e6e6e6;box-shadow:0 4px 4px -2px rgba(0,0,0,.18)}
.card-media{position:absolute;left:8px;top:8px;width:203px;height:151px}
.card-rule{position:absolute;left:20px;right:20px;top:165px;height:1px;background:#e3e3e3}
.card-title{position:absolute;left:0;right:0;top:177px;text-align:center;font:400 15px "Ubuntu",sans-serif;color:#444}
.card-text{position:absolute;left:20px;top:203px;width:190px;font:12.5px/18px "Open Sans",sans-serif;color:#555}

.promo{left:830px;top:548px;width:260px;height:505px;border-radius:3px;overflow:hidden;background:linear-gradient(var(--promo-top),var(--promo-bottom));color:var(--white);text-align:center}
.promo-curve{position:absolute;left:0;top:0}
.promo-title{position:absolute;left:0;right:0;top:21px;font:500 27px "Ubuntu",sans-serif}
.promo-price{position:absolute;left:68px;top:76px;z-index:2;font:700 70px/1 "Ubuntu",sans-serif;letter-spacing:-2px}
.promo-price sup{font-size:24px;vertical-align:top;position:relative;top:10px;margin-right:4px}
.promo-laptop{position:absolute;left:18px;top:128px;width:76px;height:50px;border-radius:4px;background:linear-gradient(#3a3f48,#1b1e24)}
.promo-phone{position:absolute;left:168px;top:130px;width:80px;height:50px;border-radius:14px;background:linear-gradient(#8d949e,#454a52)}
.promo-offer{position:absolute;left:0;right:0;top:268px;font:italic 400 32px/39px "Ubuntu",sans-serif}
.promo-button{position:absolute;left:48px;top:417px;width:171px;height:38px;border-radius:4px;background:linear-gradient(#fbfbf2,#dcdcc6);color:#333;font:500 17px/38px "Ubuntu",sans-serif;letter-spacing:-.5px;box-shadow:0 1px 2px rgba(0,0,0,.3)}

.footer{left:0;top:1079px;width:1200px;height:55px;background:linear-gradient(var(--footer-top),var(--footer-bottom))}
.copyright{position:absolute;left:121px;top:19px;font:13px "Open Sans",sans-serif;color:var(--white)}
.footer-links{position:absolute;right:109px;top:19px;font:13px "Open Sans",sans-serif;color:var(--white)}
.footer-links span{margin:0 10px}
</style>
</head>
<body>

<header>
  <div class="abs topbar"></div>
  <nav class="abs topbar-links"><a href="#">Private Customer</a><span>|</span><a href="#">Business Customer</a><span>|</span><a href="#">Housing Association</a></nav>

  <div class="abs brand"><span class="brand-dot"></span><span class="brand-name">Lunor Media</span></div>

  <div class="abs follow">Follow Us</div>
  <a class="abs social s1" href="#" aria-label="Professional network"></a>
  <a class="abs social s2" href="#" aria-label="Microblog"></a>
  <a class="abs social s3" href="#" aria-label="Social network"></a>
  <a class="abs social s4" href="#" aria-label="Email"></a>

  <nav class="abs mainnav">
    <a href="#" style="left:30px">Home</a>
    <span class="nav-sep" style="left:97px"></span>
    <a href="#" style="left:123px">Products</a>
    <span class="nav-sep" style="left:208px"></span>
    <a href="#" style="left:234px">Customer Services</a>
    <span class="nav-sep" style="left:390px"></span>
    <a href="#" style="left:415px">Lunor Media</a>
    <span class="nav-sep" style="left:525px"></span>
    <a href="#" style="left:548px">Contact Us</a>
    <div class="abs search">Search
      <svg width="18" height="18" viewBox="0 0 18 18"><circle cx="7" cy="7" r="5" fill="none" stroke="#aaa" stroke-width="2"/><line x1="11" y1="11" x2="16" y2="16" stroke="#aaa" stroke-width="2.5"/></svg>
    </div>
  </nav>
</header>

<main>
  <section class="abs hero" role="img" aria-label="Photo of a businessman in a suit using a tablet in a bright office">
    <div class="hero-line" style="top:103px">The <b>Power</b> of the next</div>
    <div class="hero-line" style="top:151px">generation <b>Lunor Media.</b></div>
  </section>

  <a class="abs service" href="#" style="top:185px">
    <span class="service-icon"><svg width="34" height="34" viewBox="0 0 34 34"><path d="M6 8 Q6 26 24 26 Z" fill="#2d6fb7"/><line x1="15" y1="17" x2="24" y2="8" stroke="#2d6fb7" stroke-width="2"/><rect x="12" y="26" width="10" height="6" fill="#2d6fb7"/></svg></span>
    <span class="service-title">Cable TV</span>
    <span class="service-text">Lorem ipsum dolor sit<br>con adipiscing elit, sed</span>
    <svg class="service-arrow" width="10" height="14" viewBox="0 0 10 14"><polyline points="2,2 8,7 2,12" fill="none" stroke="#fff" stroke-width="2.5"/></svg>
  </a>
  <a class="abs service green" href="#" style="top:273px">
    <span class="service-icon"><svg width="34" height="34" viewBox="0 0 34 34"><rect x="11" y="6" width="13" height="24" rx="3" fill="#2d6fb7"/><rect x="13" y="9" width="9" height="7" fill="#cfe6f7"/></svg></span>
    <span class="service-title">Mobile Phone</span>
    <span class="service-text">Lorem ipsum dolor sit<br>con adipiscing elit, sed</span>
    <svg class="service-arrow" width="10" height="14" viewBox="0 0 10 14"><polyline points="2,2 8,7 2,12" fill="none" stroke="#fff" stroke-width="2.5"/></svg>
  </a>
  <a class="abs service" href="#" style="top:361px">
    <span class="service-icon"><svg width="36" height="30" viewBox="0 0 36 30"><rect x="7" y="4" width="22" height="15" rx="1" fill="none" stroke="#2d6fb7" stroke-width="2.5"/><path d="M3 22 H33 L30 27 H6 Z" fill="#2d6fb7"/></svg></span>
    <span class="service-title">Broadband</span>
    <span class="service-text">Lorem ipsum dolor sit<br>con adipiscing elit, sed</span>
    <svg class="service-arrow" width="10" height="14" viewBox="0 0 10 14"><polyline points="2,2 8,7 2,12" fill="none" stroke="#fff" stroke-width="2.5"/></svg>
  </a>
  <a class="abs service" href="#" style="top:451px">
    <span class="service-icon"><svg width="34" height="34" viewBox="0 0 34 34"><rect x="8" y="14" width="14" height="12" rx="3" fill="#2d6fb7"/><line x1="4" y1="17" x2="8" y2="17" stroke="#2d6fb7" stroke-width="2.5"/><line x1="4" y1="23" x2="8" y2="23" stroke="#2d6fb7" stroke-width="2.5"/><path d="M22 20 Q30 20 28 10 Q27 5 30 3" fill="none" stroke="#2d6fb7" stroke-width="2.5"/></svg></span>
    <span class="service-title">Electricity</span>
    <span class="service-text">Lorem ipsum dolor sit<br>con adipiscing elit, sed</span>
    <svg class="service-arrow" width="10" height="14" viewBox="0 0 10 14"><polyline points="2,2 8,7 2,12" fill="none" stroke="#fff" stroke-width="2.5"/></svg>
  </a>

  <h1 class="abs welcome-title">Welcome To Lunor Media</h1>
  <div class="abs welcome-copy">
    <p>Lorem ipsum dolor sit amet, consectetur adipisicing elit, sed do eiusmod tempor incididunt ut labore et dolore magna aliqua. Ut enim ad minim veniam, quis nostrud exercitation ullamco laboris nisi ut aliquip ex ea commodo consequat. Duis aute irure dolor in reprehenderit in voluptate velit esse cillum dolore eu fugiat nulla pariatur.</p>
    <p>Excepteur sint occaecat cupidatat non proident, sunt in culpa qui officia deserunt mollit anim id est laborum.Lorem ipsum dolor sit amet, consectetur adipisicing elit, sed do eiusmod tempor incididunt ut labore et dolore magna aliqua.</p>
  </div>

  <h2 class="abs featured-title">Featured</h2>
  <div class="abs featured-rule"></div>

  <article class="abs card" style="left:120px">
    <div class="card-media" role="img" aria-label="Photo of a young woman lying on a sofa using a laptop" style="background:linear-gradient(135deg,#6b4a36,#c9a88a 60%,#e8e2da)"></div>
    <div class="card-rule"></div>
    <div class="card-title">Broadband</div>
    <p class="card-text">Lorem ipsum dolor sit amet, consectetur adipisicing elit,</p>
  </article>
  <article class="abs card" style="left:355px">
    <div class="card-media" role="img" aria-label="Photo of hanging light bulbs on a blue background, one glowing" style="background:radial-gradient(circle at 82% 58%,#d8fbff 0,#5fd8f0 12%,#0a7fa3 35%,#063f5c 100%)"></div>
    <div class="card-rule"></div>
    <div class="card-title">Electricity</div>
    <p class="card-text">Lorem ipsum dolor sit amet, consectetur adipisicing elit,</p>
  </article>
  <article class="abs card" style="left:590px">
    <div class="card-media" role="img" aria-label="Photo of a family on the floor watching television" style="background:linear-gradient(#f1eee8,#d9cfc4 55%,#a8795a)"></div>
    <div class="card-rule"></div>
    <div class="card-title">Cable T.V</div>
    <p class="card-text">Lorem ipsum dolor sit amet, consectetur adipisicing elit,</p>
  </article>

  <aside class="abs promo">
    <svg class="promo-curve" width="260" height="505" viewBox="0 0 260 505"><path d="M0 235 Q130 195 260 225 V505 H0 Z" fill="rgba(255,255,255,.1)"/></svg>
    <div class="promo-title">Internet &amp; Phone</div>
    <div class="promo-laptop" role="img" aria-label="Laptop computer"></div>
    <div class="promo-phone" role="img" aria-label="Office desk telephone"></div>
    <div class="promo-price"><sup>$</sup>75</div>
    <div class="promo-offer">Select Our<br>Broadband<br>Bundle Offer</div>
    <a class="promo-button" href="#">Start Saving Today</a>
  </aside>
</main>

<footer class="abs footer">
  <div class="copyright">Copyright © 2012 Lunor Media. All rights reserved.</div>
  <nav class="footer-links"><a href="#">Home</a><span>|</span><a href="#">Products</a><span>|</span><a href="#">Customer Services</a><span>|</span><a href="#">Lunor Media</a><span>|</span><a href="#">Contact Us</a></nav>
</footer>

</body>
</html>
```